Copper Field Agency Website - Wordpress Web UPDATED BRIEF

FINAL LOGO UPLOADED - please look to this as reference for how we would like the site to look and feel.

We are a digital marketing agency - looking to have a new website built. We are looking for a simple one page feel of site that will allow us to grow it later. (Feel free to take some liberties with that if your imagination veers off) Must be very, playful, bold, sleek and easily integrate video. Wordpress only.

Overview:

Copper Field is a creative constellation. We are built on what's great about the shared economy. With access to thousands of content creators, designers, technicians, writers, strategists and other creatives around the world, we are built differently than a traditional “brick and mortar” Marketing Agency. We provide the traditional services our clients have come to expect, without the “5X factor” of covering the overhead common in the old agency model. We believe even better work can be created in collaboration with our clients and by passing those savings back to them for their use. Our clients pay for our art, our work and our passion –not our furniture.

"Copper Field, Let's Build Together"

Target Market(s)

companies looking for creative agency help, video production, creative consulting and coaching

Industry/Entity Type

Digital Marketing

Coding

Coded - Design and coding required

Number of Pages Required

1 page

Font styles to use
Sans Serif

Colors
3277b5
33a6d7
ec1f27

Requirements
Must have
• Wordpress design is a must. Looking for a one sheet homepage - with sections that are all on the main front page. We will have videos to embed, and should be able to have client logos and easy access to show a variety of our creative work.
• Please look to the logo for how we would like the site to feel.
• Please think "icon process flow" instead of blocks of text (which we used to have). Use the text to explain what the process flow should represent - don't actually copy paste the text but show it visually in icons.
Nice to have
• innovation around how we show video content. solid colors complementary to our palette and aesthetic.
Should not have
• Standard HTML coding

```html
<!DOCTYPE html>
<html lang="en">
<head>
<meta charset="utf-8">
<title>Copper Field Agency</title>
<link href="https://fonts.googleapis.com/css2?family=Raleway:wght@600;700;800&family=Lato:wght@400;700&display=swap" rel="stylesheet">
<style>
:root{
  --blue:#3277b5;
  --sky:#33a6d7;
  --red:#ec1f27;
  --teal:#1eb1a4;
  --mauve:#b6577c;
  --navy:#0e1c33;
  --ink:#1f2a38;
  --grey:#f0f0f0;
  --brick:#a5482f;
  --brick-dark:#2b1611;
  --gold:#f4b400;
}
*{box-sizing:border-box;margin:0;padding:0}
html,body{width:1200px;height:4144px;overflow:hidden}
body{position:relative;font-family:'Lato',sans-serif;color:var(--ink);background:#fff}
.abs{position:absolute}
h2{font-family:'Raleway',sans-serif;font-weight:700;color:var(--ink)}
.btn{display:inline-block;background:var(--blue);color:#fff;font:700 15px 'Lato',sans-serif;padding:10px 18px;border-radius:3px}

/* hero */
.hero{left:0;top:0;width:1200px;height:620px}
.nav{right:40px;top:14px;display:flex;gap:22px;font:700 14px 'Lato',sans-serif;color:#fff;z-index:3}
.nav .active{color:var(--sky)}
.brand{left:150px;top:14px;display:flex;align-items:center;gap:10px;font:800 22px 'Raleway',sans-serif;color:var(--blue);z-index:3}
.brand .dot{width:44px;height:44px;border-radius:50%;background:var(--blue)}
.hero-title{left:160px;top:190px;width:470px;font:700 29px/1.3 'Raleway',sans-serif;color:var(--ink)}
.hero .btn{left:160px;top:322px}

/* about */
.about-photo{left:80px;top:675px;width:360px;height:330px;border-radius:50%;background:linear-gradient(135deg,#c46a44,#7d3b27);border:10px solid var(--blue);border-left-color:#fff;border-top-color:#fff}
.about h2{left:515px;top:690px;font-size:46px}
.about p{left:515px;top:750px;width:560px;font-size:14.5px;line-height:1.75;color:#444}
.about .btn{left:515px;top:940px}

/* services */
.services{left:0;top:1110px;width:1200px;height:760px;background:var(--grey)}
.services h2{left:110px;top:60px;font-size:44px}
.services svg{left:0;top:0}
.svc-label{font:700 22px 'Lato',sans-serif;fill:var(--ink)}

/* clients */
.clients h2{left:110px;top:1915px;font-size:44px}
.client-row{left:108px;top:2010px;display:flex;gap:20px}
.client{width:232px;height:128px;background:#fff;box-shadow:0 2px 8px rgba(0,0,0,.18);display:flex;align-items:center;justify-content:center;gap:10px;font:700 20px 'Raleway',sans-serif;color:var(--blue)}
.client i{width:26px;height:26px;background:var(--sky);border-radius:50%;display:block}
.dots{left:560px;top:2196px;display:flex;gap:10px}
.dots span{width:12px;height:12px;border-radius:50%;background:#bcd3ea}
.dots span:first-child{background:var(--blue)}

/* testimonials */
.testimonials{left:0;top:2262px;width:1200px;height:570px;background:linear-gradient(180deg,#3a1d15,var(--brick-dark))}
.testimonials h2{left:0;width:1200px;top:86px;text-align:center;color:#fff;font-size:40px;letter-spacing:1px}
.avatar{left:540px;top:180px;width:120px;height:120px;border-radius:50%;background:#5b6f82;border:5px solid #fff}
.quote{left:200px;top:262px;font:800 90px 'Raleway',sans-serif;color:var(--sky)}
.testi-text{left:300px;top:348px;width:600px;text-align:center;color:#fff;font-size:15px;line-height:1.7}
.testi-name{left:0;width:1200px;top:432px;text-align:center;color:var(--sky);font:700 13px 'Lato',sans-serif;letter-spacing:1px}
.stars{left:0;width:1200px;top:452px;text-align:center;color:var(--gold);font-size:18px;letter-spacing:3px}
.arrow{width:44px;height:44px;border-radius:50%;border:2px solid #fff;display:flex;align-items:center;justify-content:center}

/* gallery */
.gallery h2{left:0;width:1200px;top:2858px;text-align:center;font-size:44px}
.tile{background:linear-gradient(135deg,#c77752,#8d4530)}
.tile.cool{background:linear-gradient(135deg,#9fb0bf,#5b6b7a)}
.g-arrow{width:44px;height:44px;border-radius:50%;background:var(--sky);display:flex;align-items:center;justify-content:center}

/* contact */
.contact{left:0;top:3560px;width:1200px;height:584px}
.contact h2{left:0;width:1200px;top:50px;text-align:center;font-size:44px}
.foot-brand{left:120px;top:290px;display:flex;align-items:center;gap:10px;font:800 26px 'Raleway',sans-serif;color:#fff}
.foot-brand .dot{width:54px;height:54px;border-radius:50%;background:var(--blue)}
.info{left:350px;top:250px;color:#fff;font-size:14px;line-height:1.5}
.info div{display:flex;gap:12px;margin-bottom:18px;align-items:flex-start}
.links{left:640px;top:246px;color:#fff;font-size:14px;line-height:1.95}
.news{left:785px;top:246px;display:flex}
.news .field{width:250px;height:40px;background:#fff;border-radius:20px 0 0 20px;font-size:12px;color:#888;padding:12px 18px}
.news .send{width:78px;height:40px;background:var(--blue);border-radius:0 20px 20px 0;color:#fff;font:700 13px 'Lato',sans-serif;text-align:center;line-height:40px}
.social{left:800px;top:316px;display:flex;gap:22px}
.social span{width:16px;height:16px;border-radius:50%;background:#fff;display:block}
.bottom{left:0;top:4108px;width:1200px;height:36px;background:#0a1424;color:#c8d2de;font-size:12px;padding:11px 20px;display:flex;justify-content:space-between}
</style>
</head>
<body>

<section class="hero abs">
  <svg class="abs" style="left:0;top:0" width="1200" height="620" viewBox="0 0 1200 620">
    <defs>
      <linearGradient id="brick" x1="0" y1="0" x2="1" y2="1">
        <stop offset="0" stop-color="#b95538"/><stop offset="1" stop-color="#8a3c27"/>
      </linearGradient>
    </defs>
    <rect x="380" y="0" width="820" height="620" fill="url(#brick)" role="img" aria-label="Red brick wall photograph"/>
    <path d="M0 0 H520 C470 90 620 120 600 230 C580 360 700 420 880 470 C1000 505 1100 560 1200 600 V620 H0 Z" fill="#fff"/>
    <path d="M560 120 C660 60 820 110 900 200 C980 290 940 410 820 440 C700 470 600 400 580 300 C565 230 520 160 560 120 Z" fill="#eef6fb" role="img" aria-label="Digital marketing illustration with icons"/>
    <path d="M600 300 C620 420 760 470 900 480" stroke="var(--sky)" stroke-width="6" fill="none"/>
  </svg>
  <div class="brand abs"><span class="dot"></span>Copper Field</div>
  <nav class="nav abs"><span class="active">Home</span><span>About Us</span><span>Services</span><span>Our Clients</span><span>Testimonials</span><span>Gallery</span><span>Contact Us</span></nav>
  <h1 class="hero-title abs">Marketing is no longer about the stuff that you make, but about the stories you tell.</h1>
  <span class="btn abs">Contact Us</span>
</section>

<section class="about">
  <div class="about-photo abs" role="img" aria-label="Hands laying bricks with a trowel"></div>
  <h2 class="abs">About Us</h2>
  <p class="abs">Copper Field is a creative constellation. We are built on what's great about the shared economy. With access to thousands of content creators, designers, technicians, writers, strategists and other creatives around the world, we are built differently than a traditional "brick and mortar" Marketing Agency. We provide the traditional services our clients have come to expect, without the "5X factor" of covering the overhead common in the old agency model. We believe even better work can be created in collaboration with our clients and by passing those savings back to them.</p>
  <span class="btn abs">Read More</span>
</section>

<section class="services abs">
  <h2 class="abs">Services</h2>
  <svg class="abs" width="1200" height="760" viewBox="0 0 1200 760">
    <g stroke="var(--ink)" stroke-width="2" fill="none">
      <line x1="283" y1="300" x2="385" y2="300"/>
      <line x1="535" y1="300" x2="637" y2="300"/>
      <line x1="787" y1="300" x2="885" y2="300"/>
      <line x1="960" y1="375" x2="960" y2="475"/>
      <line x1="885" y1="550" x2="787" y2="550"/>
      <line x1="637" y1="550" x2="535" y2="550"/>
    </g>
    <g fill="var(--ink)">
      <circle cx="283" cy="300" r="5"/><circle cx="385" cy="300" r="5"/><circle cx="535" cy="300" r="5"/><circle cx="637" cy="300" r="5"/><circle cx="787" cy="300" r="5"/><circle cx="885" cy="300" r="5"/>
      <circle cx="960" cy="375" r="5"/><circle cx="960" cy="475" r="5"/><circle cx="885" cy="550" r="5"/><circle cx="787" cy="550" r="5"/><circle cx="637" cy="550" r="5"/><circle cx="535" cy="550" r="5"/>
    </g>
    <g font-family="Raleway, sans-serif" font-weight="700" font-size="28" text-anchor="middle" fill="#fff">
      <g><circle cx="208" cy="300" r="75" fill="#fff" stroke="var(--blue)" stroke-width="8"/><path d="M208 225 A75 75 0 0 1 208 375 Z" fill="var(--blue)"/><text x="240" y="310">1</text>
        <circle cx="172" cy="294" r="16" fill="none" stroke="var(--ink)" stroke-width="4"/><line x1="184" y1="306" x2="196" y2="318" stroke="var(--ink)" stroke-width="5"/></g>
      <g><circle cx="460" cy="300" r="75" fill="#fff" stroke="var(--teal)" stroke-width="8"/><path d="M460 225 A75 75 0 0 1 460 375 Z" fill="var(--teal)"/><text x="492" y="310">2</text>
        <circle cx="424" cy="290" r="16" fill="none" stroke="var(--ink)" stroke-width="4"/><rect x="417" y="308" width="14" height="10" fill="var(--ink)"/></g>
      <g><circle cx="712" cy="300" r="75" fill="#fff" stroke="var(--blue)" stroke-width="8"/><path d="M712 225 A75 75 0 0 1 712 375 Z" fill="var(--blue)"/><text x="744" y="310">3</text>
        <rect x="660" y="280" width="38" height="30" fill="none" stroke="var(--ink)" stroke-width="4"/><line x1="668" y1="292" x2="690" y2="292" stroke="var(--ink)" stroke-width="3"/></g>
      <g><circle cx="960" cy="300" r="75" fill="#fff" stroke="var(--mauve)" stroke-width="8"/><path d="M960 225 A75 75 0 0 1 960 375 Z" fill="var(--mauve)"/><text x="992" y="310">4</text>
        <rect x="908" y="278" width="34" height="40" fill="none" stroke="var(--ink)" stroke-width="4"/><line x1="915" y1="290" x2="935" y2="290" stroke="var(--ink)" stroke-width="3"/><line x1="915" y1="302" x2="935" y2="302" stroke="var(--ink)" stroke-width="3"/></g>
      <g><circle cx="960" cy="550" r="75" fill="#fff" stroke="var(--blue)" stroke-width="8"/><path d="M960 475 A75 75 0 0 1 960 625 Z" fill="var(--blue)"/><text x="992" y="560">5</text>
        <circle cx="925" cy="550" r="16" fill="none" stroke="var(--ink)" stroke-width="5" stroke-dasharray="6 4"/></g>
      <g><circle cx="712" cy="550" r="75" fill="#fff" stroke="var(--teal)" stroke-width="8"/><path d="M712 475 A75 75 0 0 0 712 625 Z" fill="var(--teal)"/><text x="682" y="560">6</text>
        <rect x="730" y="530" width="26" height="40" rx="4" fill="none" stroke="var(--ink)" stroke-width="4"/></g>
      <g><circle cx="460" cy="550" r="75" fill="#fff" stroke="var(--mauve)" stroke-width="8"/><path d="M460 475 A75 75 0 0 0 460 625 Z" fill="var(--mauve)"/><text x="430" y="560">7</text>
        <rect x="474" y="532" width="40" height="28" fill="none" stroke="var(--ink)" stroke-width="4"/><line x1="494" y1="560" x2="494" y2="572" stroke="var(--ink)" stroke-width="4"/></g>
    </g>
    <g class="svc-label" text-anchor="middle">
      <text x="208" y="208">Discovery</text>
      <text x="460" y="208">Strategy</text>
      <text x="712" y="184">Project</text><text x="712" y="208">Management</text>
      <text x="960" y="208">Content</text>
      <text x="960" y="662">Production</text>
      <text x="712" y="662">Paid Media</text>
      <text x="460" y="662">Coaching</text>
    </g>
  </svg>
</section>

<section class="clients">
  <h2 class="abs">Our Clients</h2>
  <div class="client-row abs">
    <div class="client"><i></i>Brightwell</div>
    <div class="client"><i></i>Lumen Co</div>
    <div class="client"><i></i>Ardent</div>
    <div class="client"><i></i>Northgate</div>
  </div>
  <div class="dots abs"><span></span><span></span><span></span></div>
</section>

<section class="testimonials abs">
  <h2 class="abs">TESTIMONIALS</h2>
  <div class="arrow abs" style="left:82px;top:250px"><svg width="16" height="16" viewBox="0 0 16 16"><path d="M11 2 L5 8 L11 14" stroke="#fff" stroke-width="2.5" fill="none"/></svg></div>
  <div class="arrow abs" style="left:1122px;top:250px"><svg width="16" height="16" viewBox="0 0 16 16"><path d="M5 2 L11 8 L5 14" stroke="#fff" stroke-width="2.5" fill="none"/></svg></div>
  <div class="avatar abs" role="img" aria-label="Client portrait"></div>
  <div class="quote abs">&ldquo;</div>
  <p class="testi-text abs">Copper Field is proving to be a force in the creative consulting industry and we look forward to collaborating with them again in the future.</p>
  <div class="testi-name abs">DANA WHITLOW, HARBOR STAGE</div>
  <div class="stars abs">★★★★★</div>
</section>

<section class="gallery">
  <h2 class="abs">Gallery</h2>
  <div class="tile abs" style="left:150px;top:2960px;width:285px;height:270px" role="img" aria-label="Bricklayer spreading mortar"></div>
  <div class="tile cool abs" style="left:440px;top:2960px;width:315px;height:270px" role="img" aria-label="Team meeting around a table"></div>
  <div class="tile abs" style="left:760px;top:2960px;width:285px;height:270px" role="img" aria-label="Office with brick walls"></div>
  <div class="tile cool abs" style="left:150px;top:3236px;width:390px;height:300px" role="img" aria-label="Designer working at a laptop"></div>
  <div class="tile abs" style="left:545px;top:3236px;width:500px;height:300px" role="img" aria-label="Bricks being laid on a wall"></div>
  <div class="g-arrow abs" style="left:66px;top:3226px"><svg width="16" height="16" viewBox="0 0 16 16"><path d="M14 8 H3 M8 3 L3 8 L8 13" stroke="#fff" stroke-width="2.5" fill="none"/></svg></div>
  <div class="g-arrow abs" style="left:1090px;top:3226px"><svg width="16" height="16" viewBox="0 0 16 16"><path d="M2 8 H13 M8 3 L13 8 L8 13" stroke="#fff" stroke-width="2.5" fill="none"/></svg></div>
</section>

<section class="contact abs">
  <svg class="abs" style="left:0;top:0" width="1200" height="584" viewBox="0 0 1200 584">
    <defs><linearGradient id="mist" x1="0" y1="0" x2="0" y2="1"><stop offset="0" stop-color="#fff"/><stop offset="1" stop-color="#cfe6f4"/></linearGradient></defs>
    <rect width="1200" height="584" fill="url(#mist)"/>
    <path d="M0 190 C300 150 520 230 760 200 C950 175 1080 160 1200 175 V584 H0 Z" fill="var(--navy)"/>
  </svg>
  <h2 class="abs">Contact Us</h2>
  <div class="foot-brand abs"><span class="dot"></span>Copper Field</div>
  <div class="info abs">
    <div><svg width="16" height="20" viewBox="0 0 16 20"><path d="M8 0 C3.5 0 0 3.5 0 8 C0 13 8 20 8 20 S16 13 16 8 C16 3.5 12.5 0 8 0 Z" fill="#fff"/><circle cx="8" cy="8" r="3" fill="var(--navy)"/></svg><span>48 Orchard Row<br>Millbrook, CA 90210</span></div>
    <div><svg width="16" height="16" viewBox="0 0 16 16"><path d="M3 1 L6 1 L7 5 L5 6.5 C6 9 7 10 9.5 11 L11 9 L15 10 L15 13 C15 14 14 15 13 15 C6 14.5 1.5 10 1 3 C1 2 2 1 3 1 Z" fill="#fff"/></svg><span>Tel: (555) 014-2288</span></div>
    <div><svg width="18" height="14" viewBox="0 0 18 14"><rect x="0" y="0" width="18" height="14" rx="2" fill="#fff"/><path d="M1 1 L9 8 L17 1" stroke="var(--navy)" stroke-width="1.6" fill="none"/></svg><span>hello@copperfield.example</span></div>
  </div>
  <div class="links abs">Home<br>About Us<br>Services<br>Our Clients<br>Testimonials<br>Gallery<br>Contact Us</div>
  <div class="news abs"><div class="field">Enter Email Address</div><div class="send">Send</div></div>
  <div class="social abs"><span></span><span></span><span></span><span></span><span></span><span></span></div>
</section>
<div class="bottom abs"><span>© 2024 All Rights Reserved | Privacy Policy | Terms and Conditions</span><span>Top</span></div>

</body>
</html>
```